Bramblewood Card Company Business Cards

We are a trading card store with Glimmorax, sports and other TCG cards, we need a business card design that encompasses a clean cut, modern style with a retro flare. website is bramblewoodcardco.com for reference. Can utilize a comic book era feel or a more modern outdoor feel to utilize the "Pacific Northwest" elements of tress, mountains, etc.

Industry/Entity Type

Trading cards and collectibles

Contact Information for Business Card

business name, email address, phone number, name, owner job title

Font styles to use
Sans Serif

```html
<!DOCTYPE html>
<html lang="en">
<head>
<meta charset="utf-8">
<title>Bramblewood Card Company – Business Cards</title>
<link href="https://fonts.googleapis.com/css2?family=Roboto:wght@400;700&display=swap" rel="stylesheet">
<style>
  :root {
    --backdrop: #3d3d3d;
    --brand-blue: #10bfe0;
    --card-white: #ffffff;
    --ink-grey: #6b6b6b;
    --text-light: #ffffff;
  }
  html, body {
    margin: 0;
    padding: 0;
    width: 1200px;
    height: 803px;
    overflow: hidden;
    background: var(--backdrop);
    font-family: "Roboto", Arial, sans-serif;
  }
  .stage {
    position: relative;
    width: 1200px;
    height: 803px;
  }
  .card {
    position: absolute;
    top: 265px;
    width: 490px;
    height: 280px;
    border-radius: 18px;
    box-sizing: border-box;
  }
  .card--front {
    left: 80px;
    background: var(--brand-blue);
    color: var(--text-light);
    display: flex;
    align-items: center;
    justify-content: center;
  }
  .card--back {
    left: 630px;
    background: var(--card-white);
    border-bottom: 3px solid var(--brand-blue);
    display: flex;
    align-items: center;
    justify-content: center;
  }
  .identity {
    text-align: right;
    padding-right: 16px;
  }
  .identity__name {
    font-size: 26px;
    font-weight: 700;
    line-height: 1.1;
    margin: 0;
  }
  .identity__title {
    font-size: 14px;
    font-weight: 400;
    margin: 2px 0 0;
  }
  .divider {
    width: 1px;
    height: 70px;
    background: rgba(255, 255, 255, 0.45);
  }
  .contacts {
    list-style: none;
    margin: 0;
    padding: 0 0 0 16px;
    font-size: 13px;
    line-height: 1.55;
  }
  .contacts__item {
    display: flex;
    align-items: center;
    gap: 7px;
  }
  .contacts__icon {
    width: 11px;
    height: 11px;
    flex: none;
  }
  .wordmark {
    display: flex;
    align-items: center;
    gap: 12px;
    color: var(--ink-grey);
    font-size: 22px;
    font-weight: 700;
    letter-spacing: 0.5px;
  }
  .wordmark__dot {
    width: 16px;
    height: 16px;
    border-radius: 50%;
    background: var(--brand-blue);
  }
</style>
</head>
<body>
<main class="stage">
  <section class="card card--front" aria-label="Business card front">
    <div class="identity">
      <p class="identity__name">Calder Voss</p>
      <p class="identity__title">President</p>
    </div>
    <div class="divider"></div>
    <ul class="contacts">
      <li class="contacts__item">
        <svg class="contacts__icon" viewBox="0 0 12 12" aria-hidden="true"><path d="M2.5 1 L4.5 1 L5.2 3.5 L4 4.5 Q5 7 7.5 8 L8.5 6.8 L11 7.5 L11 9.5 Q10.5 11 9 11 Q2 10 1 3 Q1 1.5 2.5 1 Z" fill="#fff"/></svg>
        <span>555-014-2270</span>
      </li>
      <li class="contacts__item">
        <svg class="contacts__icon" viewBox="0 0 12 12" aria-hidden="true"><rect x="0.5" y="2" width="11" height="8" fill="#fff"/><path d="M0.5 2 L6 6.5 L11.5 2" fill="none" stroke="#10bfe0" stroke-width="1.2"/></svg>
        <span>info@bramblewoodcardco.com</span>
      </li>
      <li class="contacts__item">
        <svg class="contacts__icon" viewBox="0 0 12 12" aria-hidden="true"><circle cx="6" cy="6" r="5.5" fill="#fff"/><ellipse cx="6" cy="6" rx="2.3" ry="5.5" fill="none" stroke="#10bfe0" stroke-width="0.9"/><line x1="0.5" y1="6" x2="11.5" y2="6" stroke="#10bfe0" stroke-width="0.9"/></svg>
        <span>www.bramblewoodcardco.com</span>
      </li>
    </ul>
  </section>

  <section class="card card--back" aria-label="Business card back">
    <div class="wordmark">
      <span class="wordmark__dot"></span>
      <span class="wordmark__name">Bramblewood Card Company</span>
    </div>
  </section>
</main>
</body>
</html>
```